Website for new dental office

I am Dr. Colin Ashford and am building a new dental practice. I specialize in general dentistry. I am young and have a higher end dental practice incorporating very new technologies and would like my website to reflect that. As many dental patients are older, the website must be very easy to navigate. I would like patients to be able to request appointments, and will eventually add on patient information forms (the health history, etc, that you normally fill out in the practice) from my practice management software, so leave an area for that.

Industry/Entity Type

Building

```html
<!DOCTYPE html>
<html lang="en">
<head>
<meta charset="utf-8">
<title>Colin Ashford, DDS</title>
<link href="https://fonts.googleapis.com/css2?family=Open+Sans:wght@300;400;600;700&display=swap" rel="stylesheet">
<style>
:root{
  --blue:#1b7fc0;
  --blue-dark:#0f5f99;
  --blue-light:#bfe3f7;
  --navy:#1a4c86;
  --orange:#f7821b;
  --orange-light:#fba23e;
  --ink:#333;
  --muted:#666;
  --gray:#e4e4e4;
  --white:#fff;
}
*{margin:0;padding:0;box-sizing:border-box}
html,body{width:841px;height:1200px;overflow:hidden}
body{position:relative;font-family:"Open Sans",sans-serif;color:var(--ink);background:linear-gradient(#fff 0,#fff 80px,#ececec 200px,#e8e8e8 100%)}
.abs{position:absolute}
.topbar{left:0;top:0;width:841px;height:18px;background:var(--blue-dark)}
.social{right:14px;top:2px;display:flex;gap:10px}
.social span{width:14px;height:14px;border-radius:50%;background:var(--white)}
.swoosh{left:0;top:70px}
.brand{left:77px;top:40px;font-size:26px;font-weight:400;color:#333;letter-spacing:-.3px}
.phone{left:600px;top:44px;display:flex;align-items:center;gap:6px;font-size:19px;font-weight:300;color:#444}
.page{left:77px;top:98px;width:687px;height:1056px;background:var(--white);border-radius:10px;box-shadow:0 1px 3px rgba(0,0,0,.15)}
.nav{left:77px;top:98px;width:687px;height:30px;background:linear-gradient(#2a92d2,#1472b2);border-radius:8px 8px 0 0}
.nav a{position:absolute;top:8px;font-size:11px;color:var(--white);text-decoration:none;transform:translateX(-50%)}
.nav a.active{top:7px;background:#333;padding:2px 6px;font-weight:700}
.hero{left:83px;top:134px;width:471px;height:282px;background:linear-gradient(90deg,#f3f5f7 0%,#dfe6ec 45%,#c8d4df 100%)}
.hero-title{left:238px;top:205px;font-size:20px;color:var(--navy);font-weight:400}
.hero-title b{font-weight:600}
.hero-sub{left:238px;top:232px;font-size:12.5px;color:#222;letter-spacing:.3px}
.hero-text{left:241px;top:265px;width:300px;font-size:9.5px;line-height:14px;color:#444}
.dots{left:524px;top:402px;display:flex;gap:3px}
.dots i{width:5px;height:5px;border-radius:50%;background:var(--blue)}
.dots i.on{background:#fff}
.form{left:554px;top:134px;width:203px;height:262px;background:linear-gradient(var(--orange-light),var(--orange));padding:14px 7px}
.form h2{font-size:18px;font-weight:400;color:var(--white);line-height:1}
.form h2 b{font-weight:600}
.form p{font-size:9.5px;color:#fff;line-height:11px;margin:6px 1px 11px}
.field{height:25px;background:#fff;border:1px solid #e6e6e6;margin-bottom:8px;font-size:8.5px;color:#aaa;padding:7px 6px;position:relative}
.field .caret{position:absolute;right:5px;top:8px;font-size:7px}
.submit{display:inline-block;margin-top:5px;background:#1a1a1a;color:#fff;font-size:13px;padding:6px 20px}
.wave{left:82px;top:398px}
.welcome-photo{left:84px;top:462px;width:138px;height:136px;background:linear-gradient(135deg,#e9ecef,#cdd6de);border:1px solid #ddd}
.welcome h1{font-size:18px;font-weight:400;color:#333}
.welcome{left:232px;top:460px;width:510px}
.welcome p{margin-top:6px;font-size:9.3px;line-height:14px;color:#555}
.btn{display:inline-block;margin-top:10px;background:linear-gradient(#2a92d2,#1472b2);color:#fff;font-size:12px;padding:5px 12px;border-radius:2px}
.divider{left:120px;top:612px;width:600px;height:8px;background:radial-gradient(ellipse at center top,rgba(0,0,0,.1),transparent 70%)}
.services{left:95px;top:666px;width:651px;height:164px;background:linear-gradient(#fff 0,#fff 30%,var(--blue-light) 100%);border:1px solid #e0eef6}
.svc{position:absolute;top:10px;width:134px}
.svc .ph{height:117px;border:1px solid #eee}
.svc .lbl{text-align:center;margin-top:10px;font-size:13px;color:#444}
.arrow{position:absolute;top:78px;font-size:18px;color:var(--blue);font-weight:700}
.sec-title{font-size:17px;color:var(--blue);font-weight:400}
.rule{height:3px;background:var(--blue)}
.dotted{border-top:1px dotted #bbb}
.case{position:absolute;top:905px;width:200px}
.case .ph{width:193px;height:89px;border:1px solid #ccc}
.case h3{margin-top:8px;font-size:12px;font-weight:600;color:#333;padding-bottom:3px;border-bottom:1px dotted #999;width:193px}
.case p{margin-top:10px;font-size:8.3px;line-height:11.3px;color:#666}
.case .more{position:absolute;top:212px;width:193px;border-top:1px solid #ddd;padding-top:8px;font-size:8px;font-style:italic;color:#444}
.case .more i{display:inline-block;width:9px;height:9px;background:#333;margin-left:10px;vertical-align:middle}
.testi{left:532px;top:904px;width:210px;height:133px;border:1px solid #ddd;padding:12px 13px}
.testi p{font-size:8.3px;line-height:12.5px;color:#666}
.testi .who{position:absolute;right:58px;top:66px;font-size:10px;font-weight:700;color:#111}
.quote{right:18px;top:56px;font-size:52px;line-height:1;color:#e6e6e6;font-weight:700}
.avatar{left:548px;top:993px;width:64px;height:64px;border-radius:50%;background:radial-gradient(#4a4a4a,#1f1f1f);border:4px solid #fff;box-shadow:0 0 0 1px #ddd}
.sched{left:533px;top:1079px;width:211px;height:57px;background:linear-gradient(var(--orange-light),var(--orange));padding:7px 8px}
.sched h4{font-size:12px;font-weight:600;color:#fff}
.sched p{margin-top:5px;width:150px;font-size:8px;line-height:10px;color:#fff}
.sched svg{position:absolute;right:14px;top:24px}
.footer{left:0;top:1108px;width:841px;height:92px;background:#e3e3e3;z-index:-1}
.copy{left:80px;top:1172px;font-size:9.5px;color:#333}
.links{right:80px;top:1172px;font-size:9.5px;color:#333}
</style>
</head>
<body>
<div class="abs footer"></div>
<div class="abs topbar"></div>
<div class="abs social"><span></span><span></span><span></span><span></span><span></span></div>

<svg class="abs swoosh" width="841" height="60" viewBox="0 0 841 60">
  <path d="M0 12 Q20 30 80 32 L80 38 Q20 36 0 24 Z" fill="#1b7fc0"/>
  <path d="M841 12 Q821 30 761 32 L761 38 Q821 36 841 24 Z" fill="#1b7fc0"/>
</svg>

<div class="abs brand">Colin Ashford, DDS</div>
<div class="abs phone">
  <svg width="28" height="28" viewBox="0 0 28 28"><circle cx="14" cy="14" r="12" fill="none" stroke="#1b7fc0" stroke-width="2"/><path d="M6 8c0 8 6 14 14 14l2-3-4-2-2 2c-3-1-6-4-7-7l2-2-2-4z" fill="#333"/></svg>
  <span>+123 555 0198</span>
</div>

<div class="abs page"></div>
<nav class="abs nav">
  <a class="active" style="left:40px">HOME</a>
  <a style="left:128px">ABOUT US</a>
  <a style="left:220px">SERVICES</a>
  <a style="left:315px">RESOURCES</a>
  <a style="left:410px">GALLERY</a>
  <a style="left:491px">CASES</a>
  <a style="left:565px">BLOG</a>
  <a style="left:647px">CONTACT</a>
</nav>

<div class="abs hero" role="img" aria-label="Photo of a young dentist in a white coat holding a clipboard in a bright clinic"></div>
<div class="abs hero-title">I Specialize In <b>General Dentistry</b></div>
<div class="abs hero-sub">Teeth Whitening Solutions for Everyone</div>
<p class="abs hero-text">It is a long established fact that a reader will be distracted by the readable content of a page when looking<br>at its layout.</p>
<div class="abs dots"><i></i><i class="on"></i><i></i></div>

<form class="abs form">
  <h2>Make An <b>Appointment</b></h2>
  <p>Lorem Ipsum is simply dummy text of the printing and typesetting industry.</p>
  <div class="field">Name</div>
  <div class="field">Phone</div>
  <div class="field">Email</div>
  <div class="field">Appointment Day<span class="caret">▼</span></div>
  <span class="submit">SUBMIT</span>
</form>

<svg class="abs wave" width="677" height="36" viewBox="0 0 677 36">
  <path d="M0 6 Q338 34 677 6 L677 16 Q338 44 0 16 Z" fill="#56b8ea"/>
</svg>

<div class="abs welcome-photo" role="img" aria-label="Portrait photo of the smiling dentist"></div>
<section class="abs welcome">
  <h1>Welcome to My Site</h1>
  <p>Lorem Ipsum is simply dummy text of the printing and typesetting industry. Lorem Ipsum has been the industry's standard dummy text ever since the 1500s, when an unknown printer took a galley of type and scrambled it to make a type specimen book. It has survived not only five centuries, but also the leap into electronic typesetting, remaining essentially unchanged. It was popularised in the 1960s with the release of Typeset sheets containing Lorem Ipsum passages, and more recently with desktop publishing software like Folio Layout including versions of Lorem Ipsum.</p>
  <span class="btn">Read More</span>
</section>
<div class="abs divider"></div>

<section class="abs services">
  <span class="arrow" style="left:0">‹</span>
  <div class="svc" style="left:20px"><div class="ph" role="img" aria-label="Photo of teeth with a dental mirror" style="background:linear-gradient(135deg,#e89a92,#f6e6e2)"></div><div class="lbl">Preventive</div></div>
  <div class="svc" style="left:179px"><div class="ph" role="img" aria-label="Photo of flossing teeth" style="background:linear-gradient(135deg,#e8b3a4,#f7e9e3)"></div><div class="lbl">Restorative</div></div>
  <div class="svc" style="left:338px"><div class="ph" role="img" aria-label="Photo of a bright smile" style="background:linear-gradient(135deg,#f1d8cc,#fbf1ec)"></div><div class="lbl">Cosmetic Dentistry</div></div>
  <div class="svc" style="left:497px"><div class="ph" role="img" aria-label="Photo of a denture" style="background:linear-gradient(135deg,#f4f4f4,#f0c9c2)"></div><div class="lbl">Tooth Replacement</div></div>
  <span class="arrow" style="right:2px">›</span>
</section>

<div class="abs sec-title" style="left:93px;top:864px">Case Studies</div>
<div class="abs rule" style="left:198px;top:877px;width:80px"></div>
<div class="abs dotted" style="left:280px;top:878px;width:222px"></div>

<article class="case" style="left:94px">
  <div class="ph" role="img" aria-label="Photo of a smile with red lips" style="background:linear-gradient(135deg,#f3f3f3,#d9443e 55%,#f5f5f5)"></div>
  <h3>Cosmetics</h3>
  <p>Lorem Ipsum is simply dummy text of the printing and typesetting industry. Lorem Ipsum has been the industry's standard dummy text ever since the 1500s,</p>
  <div class="more">Read more <i></i></div>
</article>
<article class="case" style="left:307px">
  <div class="ph" role="img" aria-label="Photo of a dental examination" style="background:linear-gradient(135deg,#f1e1d8,#d8b3a6 60%,#eee)"></div>
  <h3>Restorative</h3>
  <p>Lorem Ipsum is simply dummy text of the printing and typesetting industry. Lorem Ipsum has been the industry's standard dummy text ever since the 1500s,</p>
  <div class="more">Read more <i></i></div>
</article>

<div class="abs sec-title" style="left:531px;top:866px;font-size:13.5px;font-weight:600">Testimonials</div>
<div class="abs rule" style="left:626px;top:878px;width:48px;height:2px"></div>
<div class="abs dotted" style="left:675px;top:878px;width:46px"></div>
<div class="abs" style="left:727px;top:872px;width:26px;height:12px;background:#eee;border:1px solid #ddd"></div>

<div class="abs testi">
  <p>Lorem ipsum dolor slo onsec nelioro tue raliquet Morbi nec In Curabitur, lorem in design Morbi nec In Curabitur lreaoreet nisl</p>
  <div class="who">Daniel Foster</div>
  <div class="abs quote">”</div>
</div>
<div class="abs avatar" role="img" aria-label="Photo of the reviewing patient"></div>

<div class="abs sched">
  <h4>Schedule Your Appointment</h4>
  <p>Lorem Ipsum is simply dummy text of the printing and typesetting industry.</p>
  <svg width="28" height="26" viewBox="0 0 28 26" fill="none" stroke="#5a2a00" stroke-width="2"><rect x="2" y="4" width="24" height="20" rx="2"/><path d="M2 10h24M8 1v6M20 1v6"/><g fill="#5a2a00" stroke="none"><rect x="6" y="13" width="3" height="3"/><rect x="12" y="13" width="3" height="3"/><rect x="18" y="13" width="3" height="3"/><rect x="6" y="18" width="3" height="3"/><rect x="12" y="18" width="3" height="3"/><rect x="18" y="18" width="3" height="3"/></g></svg>
</div>

<div class="abs copy">Copyright © 2014 Colin Ashford, Inc</div>
<div class="abs links">Career | Support | About | Contact</div>
</body>
</html>
```